Preisliste für Kosmetikinstitut
Zielgruppe
Ich benötige für mein Kosmetikinstitut eine Preisliste für die moderne Frau, aber auch Männer. Das Design sollte mein Logo enthalten. Farben des Designkonzepts einbauen.
A4 quer zum Falten, wie ein Heft, 1. Seite Preisliste mit logo, im Innenteil dann Anwendungen
Aufgabenstellung
Minimalistisch, ästhetisch, modern, edel
Kontaktdaten auf der Rückseite
LB Hautatelier
Lotte Brenner
Lindenhang 17
83671 Waakirchen
EMail: lotte@lb-hautatelier.de
Whatsapp: 0176 284 9017

```html
<!DOCTYPE html>
<html lang="de">
<head>
<meta charset="utf-8">
<title>LB Hautatelier – Preisliste</title>
<link href="https://fonts.googleapis.com/css2?family=Poppins:wght@400;500;600;700&display=swap" rel="stylesheet">
<style>
:root{
  --backdrop:#9c9c9c;
  --paper:#fbfaf1;
  --sage:#5f6f6b;
  --sage-light:#8d9a96;
  --ink:#3f4a47;
  --row:#efede4;
  --leaf:#dfe1d8;
  --wash:#eceae0;
}
*{margin:0;padding:0;box-sizing:border-box}
html,body{width:1091px;height:1200px;overflow:hidden}
body{background:var(--backdrop);font-family:"Poppins",sans-serif;color:var(--ink);position:relative}
.page{position:absolute;width:379px;height:535px;background:var(--paper);overflow:hidden}
.page-cover{left:150px;top:67px}
.page-inner{left:546px;top:67px}
.page-back{left:356px;top:618px}
.page::before{content:"";position:absolute;inset:60px 40px 80px;background:radial-gradient(ellipse at center,var(--wash),transparent 70%);opacity:.7}
.foot-band{position:absolute;left:0;right:0;bottom:0;height:12px;background:var(--sage)}
.leaves{position:absolute;background:radial-gradient(ellipse at center,var(--leaf),transparent 72%)}
.brand{position:absolute;left:0;right:0;text-align:center;font-weight:500;color:var(--sage);letter-spacing:.5px}
.title-band{position:absolute;left:23px;top:96px;width:333px;height:31px;background:var(--sage);color:#fff;font-weight:700;font-size:22px;text-align:center;line-height:31px;letter-spacing:1px}
.frame{position:absolute;border:1.5px solid var(--sage)}
.section-head{position:absolute;left:0;right:0;text-align:center;font-weight:600;font-size:16px;color:var(--sage);line-height:18px}
.section-head span{background:var(--paper);padding:0 16px}
.item{position:absolute;left:42px}
.item h3{font-size:8.4px;font-weight:600;color:var(--sage);line-height:10px;margin-bottom:2px}
.item p{font-size:5.9px;line-height:7.6px;color:var(--ink)}
.item p+p{margin-top:7px}
.rule-v{position:absolute;width:1px;background:var(--sage)}
.rule-h{position:absolute;height:1px;background:var(--sage)}
.badge{position:absolute;display:flex;height:12px;font-size:8.2px;font-weight:600;line-height:12px;border:1px solid var(--sage)}
.badge .label{background:var(--sage);color:#fff;padding:0 3px;white-space:nowrap;flex:1;text-align:center}
.badge .price{background:var(--paper);color:var(--sage);padding:0 4px;white-space:nowrap;text-align:center}
.note{position:absolute;font-size:4px;color:var(--ink)}
.steps{position:absolute;left:42px;width:292px;font-size:5.9px;line-height:7.6px;list-style:none;counter-reset:s}
.steps li{counter-increment:s;padding-left:9px;position:relative}
.steps li::before{content:counter(s)".";position:absolute;left:0;font-weight:600}
.extras{position:absolute;left:42px;top:238px;width:296px;font-size:7px}
.extras .row{display:flex;padding:2px 8px;line-height:8px;min-height:14px;align-items:center}
.extras .row:nth-child(odd){background:var(--row)}
.extras .row span:first-child{flex:1}
.extras .row span:last-child{width:32px;font-weight:600;font-size:6.5px}
</style>
</head>
<body>

<!-- Cover / Gesichtsbehandlungen -->
<section class="page page-cover">
  <div class="leaves" style="left:0;top:0;width:80px;height:83px" role="img" aria-label="Zarte Blattzweig-Zeichnung oben links"></div>
  <div class="leaves" style="left:318px;top:0;width:61px;height:89px" role="img" aria-label="Zarte Blattzweig-Zeichnung oben rechts"></div>
  <div class="brand" style="top:34px;font-size:20px">LB Hautatelier</div>
  <div class="title-band">PREISLISTE</div>

  <div class="frame" style="left:23px;top:152px;width:332px;height:359px"></div>
  <h2 class="section-head" style="top:143px"><span>Gesichtsbehandlungen</span></h2>
  <div class="rule-v" style="left:230px;top:177px;height:309px"></div>

  <div class="item" style="top:184px;width:185px">
    <h3>Express Facial Treatment</h3>
    <p>Für alle, die wenig Zeit haben und trotzdem ihre Haut auffrischen und revitalisieren wollen.</p>
    <p>Reinigung, Enzympeeling, Serum, Maske, Abschlusspflege</p>
  </div>
  <div class="badge" style="left:243px;top:184px;width:94px"><span class="label">35-45 Min.</span><span class="price">€ 59,00</span></div>

  <div class="item" style="top:243px;width:170px">
    <h3>Classic Facial Treatment –<br>Klassische Gesichtsbehandlung</h3>
    <p>Reinigung, Enzympeeling, Vapozon, Ausreinigung, Augenbrauenkorrektur, Ampulle, Maske, individuelle Abschlusspflege</p>
  </div>
  <div class="badge" style="left:243px;top:243px;width:94px"><span class="label">45-60 Min.</span><span class="price">€ 89,00</span></div>

  <div class="item" style="top:302px;width:170px">
    <h3>Clear Skin Treatment</h3>
    <p>Die Haut wirkt ausgeglichener, Unreinheiten wird vorgebeugt, der Teint erhält Balance und kann sich beruhigen.<br>Gleichzeitig wird die Haut durch die Hyaluronsäure vitalisiert und Falten und Fältchen kann entgegengewirkt werden.</p>
  </div>
  <div class="badge" style="left:243px;top:302px;width:94px"><span class="label">50-60 Min.</span><span class="price">€ 89,00</span></div>

  <div class="item" style="top:374px;width:172px">
    <h3>Capilarine Treatment</h3>
    <p>Hautrötungen und Couperose Erscheinungen werden gelindert, die Gefäßwände werden gestärkt und das Hautbild wirkt ausgeglichener, mögliche Irritationen gehen zurück. Gleichzeitig sorgt die hochkonzentrierte Hyaluronsäure für Frische, Vitalität und Glätte.</p>
  </div>
  <div class="badge" style="left:243px;top:374px;width:94px"><span class="label">50-60 Min.</span><span class="price">€ 89,00</span></div>

  <div class="item" style="top:439px;width:172px">
    <h3>Calmisa Soft Treatment<br>(für die empfindliche, gereizte Haut)</h3>
    <p>Entzündliche Prozesse können gemildert werden, gereizte Haut oder solche, die wenig verträgt, wird beruhigt. Irritationen können zurückgehen, die Haut erhält Balance.</p>
  </div>
  <div class="badge" style="left:243px;top:439px;width:94px"><span class="label">ca. 50 Min.</span><span class="price">€ 79,00</span></div>

  <div class="foot-band"></div>
</section>

<!-- Inner page / Apparative Behandlungen -->
<section class="page page-inner">
  <div class="frame" style="left:24px;top:24px;width:331px;height:174px"></div>
  <div class="rule-v" style="left:227px;top:42px;height:83px"></div>

  <div class="item" style="top:43px;width:170px">
    <h3>Vitamin Soft Boost</h3>
    <p>Vitamine sorgen für Power und Frische in und auf der Haut, die Widerstandskraft der Haut wird gestärkt. Die Faltentiefe kann gemildert werden.</p>
  </div>
  <div class="badge" style="left:240px;top:43px;width:96px"><span class="label">ca. 50 Min.</span><span class="price">€ 79,00</span></div>

  <div class="item" style="top:98px;width:180px">
    <h3>Anti-Age Advanced</h3>
    <p>Die Haut wirkt insgesamt erfrischt, vitalisiert und gestrafft. Feine Linien und Fältchen werden reduziert.</p>
  </div>
  <div class="badge" style="left:240px;top:98px;width:96px"><span class="label">50-70 Min.</span><span class="price">€ 99,00</span></div>
  <div class="note" style="left:245px;top:113px">(je nach Peeling)</div>

  <div class="item" style="top:145px;width:292px">
    <h3>Chemisches Peeling (Oktober – April)</h3>
    <p>Professionelle Peelings können viele Problemstellungen lindern, verbessern oder gar beheben. Dazu gehören die Zellerneuerung, Glättung der Hauttextur, Reduzierung von Pigmentflecken, Verbesserung von Akne</p>
  </div>
  <div class="leaves" style="left:300px;top:178px;width:75px;height:48px" role="img" aria-label="Zarte Blattzweig-Zeichnung"></div>

  <div class="frame" style="left:24px;top:232px;width:331px;height:279px"></div>
  <h2 class="section-head" style="top:224px"><span>Apparative Behandlungen</span></h2>

  <div class="item" style="top:264px;width:190px">
    <h3>AQUAlume – „Glowing Skin" Treatment</h3>
    <p>In 6 Schritten zu einer Haut mit einmaligem Glow- Effekt</p>
  </div>
  <div class="badge" style="left:235px;top:262px;width:101px"><span class="label">60 Minuten</span><span class="price">€ 140,00</span></div>
  <ol class="steps" style="top:292px">
    <li>Behandlungsschritt: die Haut wird tiefengereinigt</li>
    <li>Behandlungsschritt: die obersten Verhornungen und Schuppen werden sanft mit einem Peeling gelöst</li>
    <li>Behandlungsschritt: die Haut wird in der Tiefe gereinigt und entschlackt</li>
    <li>Behandlungsschritt: niedermolekulare Wirkstoffe werden aufgebracht, um die Haut zu erfrischen und den entsprechenden Glow zu geben</li>
    <li>Ausgewählte und hochdosierte Wirkstoffessenzen werden auf die Haut gesprüht und durch die niedrige Molekularstruktur können diese tiefer in der Haut wirken</li>
    <li>Zum Schluss werden die Essenzen durch eine impulsgebende Druckluftmassage noch tiefer in die Haut gebracht</li>
  </ol>
  <div class="rule-h" style="left:42px;top:380px;width:295px"></div>

  <div class="item" style="top:395px;width:295px">
    <h3>Mikrodermabrasion</h3>
    <p>Bei der Mikrodermabrasion handelt es sich um ein mechanisches Hautpeeling, dabei werden mittels feinster Kristalle die Hornzellen der obersten Hautschicht schonend abgetragen und dann mit Hilfe eines Unterdrucks behutsam abgesaugt. Der revitalisierende Prozess erhöht die Durchblutung, fördert die Zellerneuerung und verleiht ihrer Haut ein zartes frisches Gefühl. Die Haut gewinnt an Spannkraft, feine Fältchen werden gemildert und Poren sichtbar verkleinert. Außerdem hilft es bei oberflächlichen Akne Narben, Pigmentstörungen und Dehnungsstreifen. Wirkstoffe können nun wieder besser von der Haut aufgenommen werden.</p>
  </div>
  <div class="badge" style="left:42px;top:471px;width:106px"><span class="label">Gesicht</span><span class="price">€ 89,00</span></div>
  <div class="badge" style="left:157px;top:471px;width:180px"><span class="label">Gesicht, Hals, Dekolleté</span><span class="price">€ 110,00</span></div>

  <div class="foot-band"></div>
</section>

<!-- Back page -->
<section class="page page-back">
  <div class="frame" style="left:24px;top:24px;width:332px;height:299px"></div>
  <div class="leaves" style="left:298px;top:6px;width:74px;height:65px" role="img" aria-label="Zarte Blattzweig-Zeichnung oben rechts"></div>

  <div class="item" style="top:46px;width:290px">
    <h3>Microneedling</h3>
    <p>Die Behandlung eignet sich besonders für Menschen, die ihre Hautqualität verbessern und Falten, (Akne)Narben, Pigmentverschiebungen, große Poren und sogar Haarausfall behandeln wollen.</p>
    <p>Mit Hilfe feinster Nadeln werden der Haut kontrolliert Mikroverletzungen zugeführt, dies regt die natürliche Wundheilung, sowie Kollagen- und Elastin Bildung an. Microneedling ist also eine natürliche Beauty-Behandlung, die körpereigene Reparaturmechanismen nutzt, um ein strafferes Hautbild zu erhalten. Bereits nach der ersten Behandlung sieht die Haut aufgepolstert, frisch und rosig aus. Kleine Linien und Fältchen werden tiefenbehandelt. Die Haut wirkt straffer und jugendlicher. Ein weiterer Vorteil, durch die Stichkanäle können Wirkstoffe besser von der Haut aufgenommen werden.</p>
  </div>
  <div class="badge" style="left:42px;top:157px;width:106px"><span class="label">Gesicht</span><span class="price">€ 110,00</span></div>
  <div class="badge" style="left:157px;top:157px;width:180px"><span class="label">Gesicht, Hals, Dekolleté</span><span class="price">€ 150,00</span></div>
  <div class="badge" style="left:42px;top:175px;width:141px"><span class="label">Gesicht, Hals</span><span class="price">€ 130,00</span></div>
  <div class="rule-h" style="left:42px;top:206px;width:295px"></div>

  <div class="item" style="top:222px"><h3>Zusatzleistungen</h3></div>
  <div class="extras">
    <div class="row"><span>Augenbrauen zupfen</span><span>€ 8</span></div>
    <div class="row"><span>Augenbrauen färben</span><span>€ 12</span></div>
    <div class="row"><span>Wimpern färben</span><span>€ 15</span></div>
    <div class="row"><span>Enthaarung störender Gesichtsbehaarung<br>mittels Wax</span><span>€ 10-30</span></div>
  </div>

  <div class="leaves" style="left:30px;top:312px;width:119px;height:116px" role="img" aria-label="Zarte Blattzweig-Zeichnung"></div>
  <div class="brand" style="top:404px;font-size:28px">LB Hautatelier</div>
  <div class="leaves" style="left:262px;top:458px;width:98px;height:65px" role="img" aria-label="Zarte Blatt-Zeichnung unten rechts"></div>

  <div class="foot-band"></div>
</section>

</body>
</html>
```